Financial investment calculator report for real estae - layout & design

I am looking to Create a web report utilizing the attached information. It is an investment calculator report that will be customized report based on an online calculator. Therefore the report will need to be designed in a manner that a backend developer will be able to build off of.

The report will need to be web based but also printed in PDF format. The report will need to include the calculation format as well as be templeted to add a report user unique profile information like Headshot, Business Logo, Name, Telephone number, email etc.

The report should be modern and clean and easy to read and use a modern clean template design. It should be able to be easily color customized by the end user to produce templets in Red, Blue, Green, and Greyscale.

The report should be no more than 3 pages total with out breaking up the sections.

Section One - Cover sheet including agent bio info, Report Title and property address (both prominent), 400 Character space for property description, Property Pictures (3), and a google Maps integration image showing property location, It should also have room for about 100 words for a text disclaimer. (I will provide text soon)

Section Two - Inputs from the calculator

Section 3 - The Four Benefits & Rates of Return

Once I have a completed/approved form I will have about a half dozen forms/reports that will need to be laid out with a similar aesthetic.

Feel free to ask me any questions. Thank You
Milo

Target Market(s)

This report will be produced by real estate agents forvtheir investor clients. It should denote professionalism

Font styles to use
Sans Serif

Colors
0054AA
0677BA
7BADD7
CADEEF
E8F1F8
00AB8E
00BBA5
67D7C9
C6EFE9
E9F9F6
EB3D1F
EC4F4E
F09395
F8D3D4
FCEDEE

```html
<!DOCTYPE html>
<html lang="en">
<head>
<meta charset="utf-8">
<title>Investment Analysis – 418 Fairhaven</title>
<link href="https://fonts.googleapis.com/css2?family=Archivo:wght@400;500;600;700;800&display=swap" rel="stylesheet">
<style>
  :root {
    --brand: #0054AA;
    --brand-mid: #0677BA;
    --brand-soft: #7BADD7;
    --brand-pale: #CADEEF;
    --brand-mist: #E8F1F8;
    --ink: #1d1d1f;
    --ink-soft: #4a4d55;
    --page: #f0f0f1;
    --card: #e1e2e5;
    --backdrop: #dcd3c9;
  }
  * { box-sizing: border-box; margin: 0; padding: 0; }
  html, body { width: 1200px; height: 800px; overflow: hidden; }
  body {
    background: var(--backdrop);
    font-family: "Archivo", Arial, sans-serif;
    color: var(--ink);
    display: flex;
    align-items: center;
    justify-content: center;
  }
  .report-page {
    position: relative;
    width: 600px;
    height: 776px;
    background: var(--page);
    box-shadow: 0 6px 24px rgba(60, 45, 30, .18);
    overflow: hidden;
  }
  .page-header {
    position: absolute; inset: 0 0 auto 0;
    height: 128px;
    background: var(--brand);
  }
  .header-meta {
    position: absolute; top: 10px;
    font-size: 6px; letter-spacing: .08em; text-transform: uppercase;
    color: var(--brand-soft);
  }
  .header-meta--left { left: 24px; }
  .header-meta--right { right: 24px; }
  .brand {
    position: absolute; left: 34px; top: 48px;
    display: flex; align-items: center; gap: 10px;
    color: #fff;
  }
  .brand-mark {
    width: 30px; height: 30px; border-radius: 50%;
    border: 2px solid #fff;
  }
  .brand-name {
    font-size: 20px; font-weight: 500; letter-spacing: .12em; text-transform: uppercase;
  }
  .agent-card {
    position: absolute; top: 28px; right: 30px;
    width: 178px; height: 200px;
    background: var(--card);
    border-radius: 12px;
    text-align: center;
    padding-top: 16px;
  }
  .agent-photo {
    width: 80px; height: 80px; margin: 0 auto 14px;
    border-radius: 50%;
    border: 2px solid var(--brand);
    background: radial-gradient(circle at 50% 40%, #c9b6a6, #6d7d92 75%);
  }
  .agent-label {
    font-size: 7px; font-weight: 700; letter-spacing: .14em; color: var(--brand); margin-bottom: 6px;
  }
  .agent-name { font-size: 10px; font-weight: 700; }
  .agent-line { font-size: 9px; color: var(--ink-soft); line-height: 1.45; }
  .title-block { position: absolute; left: 40px; top: 158px; width: 340px; }
  .report-title { font-size: 27px; font-weight: 800; letter-spacing: .01em; }
  .property-address { font-size: 30px; font-weight: 800; color: var(--brand); line-height: 1.05; margin-top: 2px; }
  .property-type { font-size: 13px; font-weight: 500; color: var(--brand); margin-top: 4px; }
  .about { position: absolute; left: 40px; top: 266px; width: 330px; }
  .section-label {
    font-size: 7px; font-weight: 600; letter-spacing: .2em; text-transform: uppercase; color: #6c6f76;
    margin-bottom: 6px;
  }
  .about p { font-size: 9.5px; font-weight: 500; line-height: 1.4; }
  .photo-row {
    position: absolute; left: 40px; right: 40px; top: 340px;
    display: flex; gap: 12px;
  }
  .photo {
    flex: 1; height: 122px; border-radius: 10px;
    border: 3px solid #fff;
    box-shadow: 0 1px 4px rgba(0,0,0,.12);
  }
  .photo--exterior { background: linear-gradient(180deg, #7f86b8 0%, #c7a9c3 45%, #4e5a74 75%, #577a3e 100%); }
  .photo--living { background: linear-gradient(135deg, #0d5a8f 0%, #1d74a8 55%, #8a6745 100%); }
  .photo--lounge { background: linear-gradient(160deg, #d9dde0 0%, #b9c2c8 60%, #8e979c 100%); }
  .map {
    position: absolute; left: 40px; right: 40px; top: 476px; height: 150px;
    border-radius: 10px; border: 2px solid #fff;
    background: linear-gradient(120deg, #e7e9ea 0%, #dfe4e2 60%, #e6e8e6 100%);
  }
  .disclaimer {
    position: absolute; left: 0; right: 0; top: 644px; height: 104px;
    background: var(--brand);
    color: #fff;
    padding: 22px 40px 0;
  }
  .disclaimer .section-label { color: var(--brand-soft); }
  .disclaimer p { font-size: 9.5px; line-height: 1.45; width: 470px; }
  .page-number { position: absolute; right: 24px; top: 12px; font-size: 8px; color: #fff; }
  .page-footer {
    position: absolute; left: 24px; bottom: 9px;
    font-size: 8px; color: var(--ink);
  }
</style>
</head>
<body>
  <article class="report-page">
    <header class="page-header">
      <span class="header-meta header-meta--left">Report 2024</span>
      <span class="header-meta header-meta--right">Page One</span>
      <div class="brand">
        <span class="brand-mark"></span>
        <span class="brand-name">Harbor Point Realty</span>
      </div>
    </header>

    <aside class="agent-card">
      <div class="agent-photo" role="img" aria-label="Agent headshot"></div>
      <div class="agent-label">AGENT</div>
      <div class="agent-name">Dana Whitfield</div>
      <div class="agent-line">admin1</div>
      <div class="agent-line">(555) 014-2290</div>
      <div class="agent-line">dana@harborpoint.example</div>
    </aside>

    <section class="title-block">
      <h1 class="report-title">Investment Analysis</h1>
      <h2 class="property-address">418 Fairhaven</h2>
      <p class="property-type">15-Plex of 1bd/1bth Apartments</p>
    </section>

    <section class="about">
      <h3 class="section-label">About the property</h3>
      <p>Lorem ipsum is a placeholder text commonly used to demonstrate the visual form of a document or a typeface without relying on meaningful content.</p>
    </section>

    <section class="photo-row">
      <div class="photo photo--exterior" role="img" aria-label="Property exterior photo"></div>
      <div class="photo photo--living" role="img" aria-label="Interior living room photo"></div>
      <div class="photo photo--lounge" role="img" aria-label="Interior lounge photo"></div>
    </section>

    <div class="map" role="img" aria-label="Map showing the property location"></div>

    <section class="disclaimer">
      <span class="page-number">1/3</span>
      <h3 class="section-label">Disclaimer</h3>
      <p>In publishing and graphic design, Lorem ipsum is a placeholder text commonly used to demonstrate the visual form of a document or a typeface without relying on meaningful content. Lorem ipsum may be used as a placeholder before final copy is available.</p>
    </section>

    <footer class="page-footer">https://www.propertyfigures.example/report/pdf/5</footer>
  </article>
</body>
</html>
```